Staff Newsletter Template Image

We are looking for two .jpg images that we can put into a Word document and use for our staff newsletter. We will then add content using text boxes.
Attached is the current template which works for the columns and size that we need but we just want a fresh new design.
The Word document shows how we use it.
The name will stay the same - Brightwave Post but can be a different look to the current one.

Target Market(s)

Sales team

Colors

Designer to choose colors to be used in the design.

Requirements
Must have
• Colours will be green, grey and white, possibly cream if needed. All from the guidelines.
• I have attached our brand guidelines which shows design elements and fonts for our brand. Also attached is brand guidelines for one of our product lines as we would like to use the same green.
• It needs to be nice to look at and motivational for our team

```html
<!DOCTYPE html>
<html lang="en">
<head>
<meta charset="utf-8">
<title>Brightwave Post – Newsletter Pages</title>
<link rel="stylesheet" href="https://fonts.googleapis.com/css2?family=Raleway:wght@400&display=swap">
<style>
  :root {
    --backdrop: #dcdcdc;
    --brand-green: #8cc544;
    --brand-green-deep: #5a8a2c;
    --slate: #4d4b4c;
    --paper: #ffffff;
  }
  * { margin: 0; padding: 0; box-sizing: border-box; }
  html, body {
    width: 1200px;
    height: 1000px;
    overflow: hidden;
    background: var(--backdrop);
  }
  .spread {
    position: relative;
    width: 1200px;
    height: 1000px;
  }
  .page {
    position: absolute;
    top: 183px;
    width: 448px;
    height: 634px;
    display: block;
  }
  .page--front { left: 120px; }
  .page--back { left: 633px; }
  .masthead-title {
    font-family: "Raleway", sans-serif;
    font-weight: 400;
    font-size: 44px;
    fill: var(--paper);
    letter-spacing: 0.5px;
  }
  .fill-green { fill: var(--brand-green); }
  .fill-slate { fill: var(--slate); }
  .fill-paper { fill: var(--paper); }
</style>
</head>
<body>
<main class="spread">

  <!-- Front page: masthead and two content columns -->
  <svg class="page page--front" viewBox="0 0 672 950" preserveAspectRatio="none" aria-label="Brightwave Post front page">
    <defs>
      <linearGradient id="mastheadGradient" x1="0" y1="0" x2="0" y2="1">
        <stop offset="0" stop-color="var(--brand-green-deep)"/>
        <stop offset="0.7" stop-color="var(--brand-green)"/>
        <stop offset="1" stop-color="var(--brand-green)"/>
      </linearGradient>
    </defs>
    <rect class="masthead" x="0" y="0" width="672" height="230" fill="url(#mastheadGradient)"/>

    <!-- top diagonal bands -->
    <polygon class="fill-slate" points="0,136 336,170 336,186 0,151"/>
    <polygon class="fill-paper" points="336,169 672,201 672,218 336,186"/>

    <!-- left column -->
    <polygon class="fill-paper column column--left" points="0,151 336,186 336,950 0,950"/>
    <!-- right column -->
    <polygon class="fill-slate column column--right" points="336,185 672,217 672,950 336,950"/>

    <!-- bottom diagonal bands -->
    <polygon class="fill-slate" points="0,856 336,889 336,903 0,871"/>
    <polygon class="fill-green" points="0,871 336,903 336,950 0,950"/>
    <polygon class="fill-green" points="336,889 672,921 672,935 336,903"/>
    <polygon class="fill-paper" points="336,903 672,935 672,950 336,950"/>

    <text class="masthead-title" x="332" y="118" text-anchor="middle">Brightwave Post</text>
  </svg>

  <!-- Back page: two content columns -->
  <svg class="page page--back" viewBox="0 0 672 950" preserveAspectRatio="none" aria-label="Brightwave Post back page">
    <rect class="fill-green column column--left" x="0" y="0" width="336" height="950"/>
    <rect class="fill-paper column column--right" x="336" y="0" width="336" height="950"/>

    <!-- bottom diagonal bands -->
    <polygon class="fill-paper" points="0,854 336,886 336,900 0,868"/>
    <polygon class="fill-slate" points="0,868 336,900 336,950 0,950"/>
    <polygon class="fill-slate" points="336,888 672,919 672,934 336,902"/>
    <polygon class="fill-green" points="336,902 672,934 672,950 336,950"/>
  </svg>

</main>
</body>
</html>
```